Redesign of business card for Cedar Ridge Mechanical

We are looking for a new design for our business cards for Cedar Ridge Mechanical. We are a plumbing & HVAC construction company, operating on the West Coast of Canada and USA. Logo attached.
Industry/Entity Type
Construction - Plumbing & HVAC
Contact Information for Business Card
Name, address, phone numbers, email, website address
Look and feel
Each slider illustrates characteristics of the customer's brand and the style your logo design should communicate.

```html
<!DOCTYPE html>
<html lang="en">
<head>
<meta charset="utf-8">
<title>Cedar Ridge Mechanical – Business Card</title>
<link href="https://fonts.googleapis.com/css2?family=Montserrat:wght@400;700&display=swap" rel="stylesheet">
<style>
  :root {
    --backdrop: #d3d7d6;
    --card-light: #efeeea;
    --card-dark: #0c0c0c;
    --ink: #111111;
    --ink-soft: #3a3a3a;
    --paper-white: #f4f4f2;
  }
  * { box-sizing: border-box; margin: 0; padding: 0; }
  html, body {
    width: 1200px; height: 881px; overflow: hidden;
    background: var(--backdrop);
    font-family: "Montserrat", sans-serif;
  }
  .card-set {
    position: absolute; inset: 0;
    display: flex; align-items: center; justify-content: center; gap: 40px;
  }
  .card {
    position: relative;
    width: 540px; height: 309px;
    border-radius: 3px;
    box-shadow: 0 10px 28px rgba(0,0,0,0.18);
  }
  .card--front { background: var(--card-light); color: var(--ink); }
  .card--back { background: var(--card-dark); color: var(--paper-white); }

  .identity {
    position: absolute; left: 52px; top: 92px; width: 200px;
    text-align: right;
  }
  .identity__name { font-weight: 700; font-size: 19px; letter-spacing: 0.5px; }
  .identity__role { font-weight: 400; font-size: 13px; color: var(--ink-soft); margin-top: 4px; }

  .divider {
    position: absolute; left: 272px; top: 90px;
    width: 1.5px; height: 62px; background: var(--ink);
  }

  .contacts {
    position: absolute; left: 290px; top: 92px;
    list-style: none; font-size: 13px; color: var(--ink-soft);
  }
  .contacts li { display: flex; align-items: center; gap: 7px; line-height: 20px; }
  .contacts svg { width: 11px; height: 11px; fill: var(--ink); flex: none; }

  .brand-mini {
    position: absolute; right: 28px; top: 26px;
    display: flex; align-items: center; gap: 6px;
    font-weight: 700; font-size: 10px; letter-spacing: 0.5px; color: var(--ink);
  }
  .brand-mini__square { width: 10px; height: 10px; background: var(--ink); }

  .address {
    position: absolute; left: 52px; bottom: 60px;
    font-size: 13px; color: var(--ink-soft);
  }

  .brand-large {
    position: absolute; inset: 0;
    display: flex; flex-direction: column; align-items: center; justify-content: center; gap: 18px;
  }
  .brand-large__square { width: 40px; height: 40px; background: var(--paper-white); }
  .brand-large__name {
    font-weight: 700; font-size: 24px; letter-spacing: 3px; text-transform: uppercase;
  }
</style>
</head>
<body>
  <main class="card-set">
    <section class="card card--front" aria-label="Card front">
      <div class="brand-mini">
        <span class="brand-mini__square"></span>
        <span>Cedar Ridge Mechanical</span>
      </div>
      <div class="identity">
        <p class="identity__name">DANIEL HARPER</p>
        <p class="identity__role">Managing Director</p>
      </div>
      <div class="divider"></div>
      <ul class="contacts">
        <li>
          <svg viewBox="0 0 24 24"><path d="M6.6 10.8a15 15 0 0 0 6.6 6.6l2.2-2.2a1 1 0 0 1 1-.25 11.4 11.4 0 0 0 3.6.57 1 1 0 0 1 1 1V20a1 1 0 0 1-1 1A17 17 0 0 1 3 4a1 1 0 0 1 1-1h3.5a1 1 0 0 1 1 1c0 1.25.2 2.45.57 3.57a1 1 0 0 1-.25 1z"/></svg>
          <span>123 456 789</span>
        </li>
        <li>
          <svg viewBox="0 0 24 24"><path d="M2 5h20v14H2z M4 7v.5l8 5 8-5V7l-8 5z" fill-rule="evenodd"/></svg>
          <span>info@yourgmail.com</span>
        </li>
        <li>
          <svg viewBox="0 0 24 24"><circle cx="12" cy="12" r="10"/></svg>
          <span>www.yourwebsite.com</span>
        </li>
      </ul>
      <p class="address">Your address, City State, Zip 1234</p>
    </section>

    <section class="card card--back" aria-label="Card back">
      <div class="brand-large">
        <span class="brand-large__square"></span>
        <span class="brand-large__name">Cedar Ridge Mechanical</span>
      </div>
    </section>
  </main>
</body>
</html>
```